Healthy lifestyle Influencer business card

I need your creativity to have a business card that I can leave in all the restaurants, hotels and spas I visit to inform them that I am an influencer specializing in the wellness sector and that I will write a review about them. You can use my instagram photos Lunavita27 or on my website www.piattileggeriorto.it. I would like my business card to impress with its creativity! thank you very much!

Contact Information for Business Card

siteweb, instagram, phone number

Font styles to use
Decorative
Script

Colors
0094D4
00A9DD
6FCCEA
C7EBF8
E9F6FB
59FF00
82FF00
B8FF75
E3FFCB
F4FFEA
FFC000
F8CF3A
FAE287
FDF2CF
FEFAEE
F0912C
F2A743
F7CA91
FBE8D2
FDF5EE
EE7325
F08F49
F5BC92
FAE3D3
FDF4ED
EB3D1F
EC4F4E
F09395
F8D3D4
FCEDEE
E54698
E96AAD
F1A4CE
F9D9EA
FCEFF6

Requirements
Nice to have
• creativity

```html
<!DOCTYPE html>
<html lang="it">
<head>
<meta charset="utf-8">
<title>Luna Vita Kitchen – Business Card</title>
<link href="https://fonts.googleapis.com/css2?family=Montserrat:wght@400;500;700&display=swap" rel="stylesheet">
<style>
  :root {
    --backdrop: #9a9a9a;
    --card-grey: #575757;
    --peach: #f0d3b8;
    --peach-deep: #e8c4a2;
    --white: #ffffff;
    --ink: #4a4a4a;
    --tagline-back: #c4c4c4;
  }
  * { margin: 0; padding: 0; box-sizing: border-box; }
  html, body {
    width: 1133px; height: 1200px; overflow: hidden;
    background: var(--backdrop);
    font-family: "Montserrat", sans-serif;
  }
  .card {
    position: absolute;
    width: 723px; height: 412px;
    background: var(--card-grey);
    overflow: hidden;
  }
  .card--front { left: 197px; top: 144px; }
  .card--back { left: 202px; top: 640px; height: 411px; width: 719px; }

  .contact { position: absolute; left: 42px; top: 178px; color: var(--white); }
  .contact__name {
    font-weight: 700; font-size: 21px; letter-spacing: 0.5px;
    color: var(--peach); line-height: 1;
  }
  .contact__role { font-size: 15px; margin-top: 5px; }
  .contact__address { font-size: 15px; line-height: 20px; margin-top: 19px; }
  .contact__list { list-style: none; margin-top: 10px; font-size: 15px; }
  .contact__item { display: flex; align-items: center; height: 20.5px; }
  .contact__icon { width: 13px; height: 13px; margin-right: 9px; flex: none; }

  .feature-area {
    position: absolute; left: 283px; top: 37px; width: 460px; height: 400px;
    border-radius: 48% 0 0 52% / 55% 0 0 45%;
    background: radial-gradient(ellipse at 62% 50%, var(--white) 62%, var(--peach) 78%, var(--peach-deep) 100%);
  }

  .brand { position: absolute; text-align: center; }
  .brand__name { font-weight: 400; line-height: 1; white-space: nowrap; }
  .brand__tagline { font-size: 14px; line-height: 1; white-space: nowrap; }

  .card--front .brand { left: 386px; width: 300px; top: 258px; }
  .card--front .brand__name { font-size: 28px; color: var(--ink); }
  .card--front .brand__tagline { color: var(--ink); margin-top: 18px; }

  .card--back .brand { left: 0; width: 100%; top: 172px; }
  .card--back .brand__name { font-size: 38px; color: var(--white); }
  .card--back .brand__tagline { font-size: 18px; font-weight: 500; color: var(--tagline-back); margin-top: 26px; }
</style>
</head>
<body>
  <section class="card card--front">
    <div class="contact">
      <p class="contact__name">ELENA MARCHI</p>
      <p class="contact__role">President</p>
      <p class="contact__address">1420 Willow Crest Road<br>Juneau, Alaska 34810</p>
      <ul class="contact__list">
        <li class="contact__item">
          <svg class="contact__icon" viewBox="0 0 16 16"><path fill="#f0d3b8" d="M3.6 1.2l2.3 2.6-1.3 1.9c.9 2 2.6 3.8 4.7 4.8l1.9-1.3 2.6 2.3-1.3 2.3C7.5 13.4 2.6 8.5 1.2 3.5z"/></svg>
          555.318.2046
        </li>
        <li class="contact__item">
          <svg class="contact__icon" viewBox="0 0 16 16"><rect x="1" y="3.5" width="14" height="9" rx="1" fill="#f0d3b8"/><path d="M1.5 4l6.5 5 6.5-5" stroke="#575757" stroke-width="1.3" fill="none"/></svg>
          info@piattileggeriorto.it
        </li>
        <li class="contact__item">
          <svg class="contact__icon" viewBox="0 0 16 16"><circle cx="8" cy="8" r="6.5" fill="none" stroke="#f0d3b8" stroke-width="1.6"/><path d="M1.5 8h13M8 1.5c-3 3.5-3 9.5 0 13M8 1.5c3 3.5 3 9.5 0 13" stroke="#f0d3b8" stroke-width="1.2" fill="none"/></svg>
          piattileggeriorto.it
        </li>
        <li class="contact__item">
          <svg class="contact__icon" viewBox="0 0 16 16"><circle cx="8" cy="8" r="6" fill="#f0d3b8"/></svg>
          @lunavita27
        </li>
      </ul>
    </div>
    <div class="feature-area" role="img" aria-label="Large brush-painted heart in peach and white"></div>
    <div class="brand">
      <p class="brand__name">Luna Vita Kitchen</p>
      <p class="brand__tagline">benessere a ogni boccone</p>
    </div>
  </section>

  <section class="card card--back">
    <div class="brand">
      <p class="brand__name">Luna Vita Kitchen</p>
      <p class="brand__tagline">benessere a ogni boccone</p>
    </div>
  </section>
</body>
</html>
```